body balm label design

body balm tube design, current label design for other similar products
Need to have a design which can interchange between 3 different solutions
Amber Tide (Lavender + Vanilla)
Copper Ridge (Eucalyptus + Mint)
Fern Hollow (Bergamot + Cedarwood)
Tube size:
2.5h x 3.25 w
Target Market(s)
natural, solution focused
Requirements
Must have
- relatable to existing brand designs, focus on features and benefits

```html
<!DOCTYPE html>
<html lang="en">
<head>
<meta charset="utf-8">
<title>Willow Bloom Natural Body Balm Labels</title>
<link href="https://fonts.googleapis.com/css2?family=Playfair+Display:wght@400&family=Allura&family=Montserrat:wght@300;400;600&display=swap" rel="stylesheet">
<style>
  :root {
    --page-bg: #eef0f4;
    --label-bg: #ffffff;
    --amber: #8497a4;
    --copper: #6f9e58;
    --fern: #b7c9a8;
    --text-soft: #9aa5ad;
  }
  * { box-sizing: border-box; margin: 0; padding: 0; }
  html, body {
    width: 1059px; height: 1200px; overflow: hidden;
    background: var(--page-bg);
  }
  .sheet {
    position: relative; width: 1059px; height: 1200px;
    display: flex; flex-direction: column; align-items: center;
    justify-content: center; gap: 30px;
  }
  .label {
    position: relative; width: 470px; height: 360px;
    background: var(--label-bg); overflow: hidden;
    color: var(--accent);
  }
  .label--amber { --accent: var(--amber); }
  .label--fern { --accent: var(--fern); }
  .label--copper { --accent: var(--copper); }

  .botanical {
    position: absolute; left: 20px; top: 10px; width: 320px; height: 345px;
  }
  .title {
    position: absolute; right: 137px; top: 46px;
    font-family: "Playfair Display", serif; font-weight: 400;
    font-size: 58px; letter-spacing: 5px; line-height: 1;
  }
  .title-rule {
    position: absolute; left: 0; top: 121px; width: 262px; height: 2px;
    background: var(--accent);
  }
  .subtitle {
    position: absolute; right: 158px; top: 108px;
    font-family: "Allura", cursive; font-size: 26px; line-height: 1;
  }
  .band {
    position: absolute; left: 0; top: 140px; width: 339px; height: 73px;
    background: var(--accent); border-radius: 0 37px 37px 0;
    color: #fff;
  }
  .band-name {
    position: absolute; left: 0; width: 312px; top: 9px;
    text-align: center; font-family: "Montserrat", sans-serif; font-weight: 300;
    font-size: 23px; line-height: 29px; letter-spacing: 1px;
  }
  .brand-mark {
    position: absolute; left: 270px; top: 18px; width: 56px;
    display: flex; flex-direction: column; align-items: center; gap: 4px;
    font-family: "Montserrat", sans-serif; font-weight: 400; font-size: 6px;
    letter-spacing: 0.5px; text-align: center; line-height: 1.2;
  }
  .brand-mark .dot {
    width: 16px; height: 16px; border-radius: 50%; border: 1px solid #fff;
  }
  .scent {
    position: absolute; left: 0; width: 390px; top: 222px; text-align: center;
    font-family: "Allura", cursive; font-size: 38px; line-height: 1;
  }
  .net-wt {
    position: absolute; left: 80px; top: 305px;
    font-family: "Montserrat", sans-serif; font-weight: 300; font-size: 12px;
  }
  .origin-seal {
    position: absolute; left: 270px; top: 283px; width: 56px; height: 56px;
    border: 1px solid var(--accent); border-radius: 50%;
  }
  .details {
    position: absolute; left: 374px; top: 60px; width: 88px;
    font-family: "Montserrat", sans-serif; font-size: 7.6px; line-height: 9.6px;
    letter-spacing: 0.4px; color: var(--accent);
  }
  .details h3 { font-weight: 600; font-size: 7.6px; margin-bottom: 1px; }
  .details p { font-weight: 300; margin-bottom: 9px; }
  .social {
    position: absolute; left: 375px; top: 293px; display: flex; gap: 8px;
  }
  .social span {
    width: 14px; height: 14px; border-radius: 50%; background: var(--accent);
  }
  .maker {
    position: absolute; left: 354px; top: 314px; width: 116px; text-align: center;
    font-family: "Montserrat", sans-serif; font-weight: 300; font-size: 7.6px;
    line-height: 11px; letter-spacing: 0.4px;
  }
  .maker .web { font-weight: 600; }
</style>
</head>
<body>
<main class="sheet">

  <article class="label label--amber">
    <svg class="botanical" role="img" aria-label="Line illustration of lavender and vanilla botanicals" viewBox="0 0 320 345">
      <ellipse cx="160" cy="172" rx="155" ry="168" fill="#8497a4" opacity="0.08"/>
    </svg>
    <h1 class="title">AMBER</h1>
    <div class="title-rule"></div>
    <div class="subtitle">tide</div>
    <div class="band">
      <div class="band-name">NATURAL<br>BODY BALM</div>
      <div class="brand-mark"><span class="dot"></span>WILLOW BLOOM</div>
    </div>
    <div class="scent">Lavender + Vanilla</div>
    <div class="net-wt">NET WT 4 oz /120g</div>
    <div class="origin-seal"></div>
    <div class="details">
      <h3>Ingredients:</h3>
      <p>Shea butter, cocoa butter, coconut oil, sweet almond oil, beeswax, lavender essential oil, vanilla extract or vanilla oleoresin, vitamin E oil</p>
      <h3>How to use:</h3>
      <p>Scoop a small amount, warm it between your palms, apply to dry skin areas, gently massage in, let it absorb, use as needed.</p>
    </div>
    <div class="social"><span></span><span></span><span></span></div>
    <div class="maker">Made by Willow Bloom<br><span class="web">WWW.WILLOWBLOOM.CA</span></div>
  </article>

  <article class="label label--fern">
    <svg class="botanical" role="img" aria-label="Line illustration of bergamot fruit and cedar botanicals" viewBox="0 0 320 345">
      <ellipse cx="160" cy="172" rx="155" ry="168" fill="#b7c9a8" opacity="0.14"/>
    </svg>
    <h1 class="title">FERN</h1>
    <div class="title-rule"></div>
    <div class="subtitle">hollow</div>
    <div class="band">
      <div class="band-name">NATURAL<br>BODY BALM</div>
      <div class="brand-mark"><span class="dot"></span>WILLOW BLOOM</div>
    </div>
    <div class="scent">Bergamot + Cedarwood</div>
    <div class="net-wt">NET WT 4 oz /120g</div>
    <div class="origin-seal"></div>
    <div class="details">
      <h3>Ingredients:</h3>
      <p>Shea butter, cocoa butter, coconut oil, sweet almond oil, beeswax, lavender essential oil, vanilla extract or vanilla oleoresin, vitamin E oil</p>
      <h3>How to use:</h3>
      <p>Scoop a small amount, warm it between your palms, apply to dry skin areas, gently massage in, let it absorb, use as needed.</p>
    </div>
    <div class="social"><span></span><span></span><span></span></div>
    <div class="maker">Made by Willow Bloom<br><span class="web">WWW.WILLOWBLOOM.CA</span></div>
  </article>

  <article class="label label--copper">
    <svg class="botanical" role="img" aria-label="Line illustration of eucalyptus and mint leaves" viewBox="0 0 320 345">
      <ellipse cx="160" cy="172" rx="155" ry="168" fill="#6f9e58" opacity="0.08"/>
    </svg>
    <h1 class="title">COPPER</h1>
    <div class="title-rule"></div>
    <div class="subtitle">ridge</div>
    <div class="band">
      <div class="band-name">NATURAL<br>BODY BALM</div>
      <div class="brand-mark"><span class="dot"></span>WILLOW BLOOM</div>
    </div>
    <div class="scent">Eucalyptus + Mint</div>
    <div class="net-wt">NET WT 4 oz /120g</div>
    <div class="origin-seal"></div>
    <div class="details">
      <h3>Ingredients:</h3>
      <p>Shea butter, cocoa butter, coconut oil, sweet almond oil, beeswax, lavender essential oil, vanilla extract or vanilla oleoresin, vitamin E oil</p>
      <h3>How to use:</h3>
      <p>Scoop a small amount, warm it between your palms, apply to dry skin areas, gently massage in, let it absorb, use as needed.</p>
    </div>
    <div class="social"><span></span><span></span><span></span></div>
    <div class="maker">Made by Willow Bloom<br><span class="web">WWW.WILLOWBLOOM.CA</span></div>
  </article>

</main>
</body>
</html>
```